UI/ UX Design for ERP Software

We need a new UX/UI interface for a ERP software for property managers. Our CMMS / ERP solution is made based on responsive design technologies and is coded in PHP.
The overall UX to be similar to Tev Ulna - easy navigation, intuitive menus.

Industry/Entity Type

Property Management

Number of Pages Required

5+ page

Requirements
Must have
• Round dock buttons
Consistent icons across the application
Enough Spacing between buttons/icons/ menu
Consistent Font
Nice to have
• We would like the UX to allow the users to use the application without /minimum training.
Should not have
• we don't want anything that is classic with respect to UX

```html
<!DOCTYPE html>
<html lang="en">
<head>
<meta charset="utf-8">
<title>Keyhold Dashboard</title>
<link href="https://fonts.googleapis.com/css2?family=Open+Sans:wght@400;600&display=swap" rel="stylesheet">
<style>
:root{
  --page:#f4f4f4;
  --header:#525f74;
  --header-btn:#2f3f58;
  --white:#ffffff;
  --ink:#1e1e1e;
  --muted:#6c6c6c;
  --grid:#e2e2e2;
  --blue:#0a84f5;
  --dark:#3d3f45;
  --violet:#8181ef;
  --pink:#ef5a80;
  --orange:#f89b50;
  --yellow:#e3cf55;
  --footer:#000000;
}
*{margin:0;padding:0;box-sizing:border-box}
html,body{width:1200px;height:645px;overflow:hidden}
body{font-family:"Open Sans",sans-serif;background:var(--page);position:relative;color:var(--ink)}
.abs{position:absolute}
.topbar{left:0;top:0;width:1200px;height:52px;background:var(--header)}
.brand{left:0;top:0;width:202px;height:52px;background:var(--white);display:flex;align-items:center;justify-content:center;gap:8px}
.brand-dot{width:16px;height:16px;border-radius:50%;background:var(--blue)}
.brand-name{font-size:22px;font-weight:600;color:var(--blue)}
.btn{top:14px;height:28px;display:flex;align-items:center;justify-content:center;gap:7px;color:var(--white);font-size:11px;font-weight:600}
.btn-dashboard{left:233px;width:103px;background:var(--header-btn)}
.btn-reports{left:351px;width:106px;border:1.5px solid var(--white);font-weight:400}
.nav{left:530px;top:0;height:52px;display:flex;align-items:center;gap:17px;color:var(--white);font-size:11px}
.nav span{display:flex;align-items:center;gap:4px}
.burger{left:1142px;top:19px}
.card{background:var(--white);border-radius:8px}
.activity{left:42px;top:93px;width:785px;height:414px}
.side{left:860px;top:92px;width:298px;height:418px}
.title-icon{left:58px;top:127px;width:26px;height:26px;border-radius:50%;background:var(--white);box-shadow:0 1px 4px rgba(0,0,0,.1);display:flex;align-items:center;justify-content:center}
.title{left:95px;top:128px;font-size:14px}
.tabs{left:302px;top:124px;width:483px;height:27px;border-bottom:1px solid var(--grid);display:flex;justify-content:space-between;font-size:11px;color:var(--muted)}
.tabs .active{color:var(--blue);border-bottom:2px solid var(--blue);height:27px}
.chart{left:0;top:0}
.legend{font-size:10px;color:var(--ink)}
.legend .dot{position:absolute;width:11px;height:11px;border-radius:50%}
.legend .lbl{position:absolute;white-space:nowrap}
.stat{left:896px;width:227px;height:83px;background:var(--white);border-radius:6px;box-shadow:0 1px 6px rgba(0,0,0,.06)}
.stat .ring{position:absolute;left:22px;top:15px}
.stat .name{position:absolute;left:95px;top:20px;font-size:14px}
.stat .value{position:absolute;left:95px;top:43px;font-size:12px;color:#3a3a3a}
.stat-total{background:var(--violet);color:var(--white)}
.stat-total .value{color:var(--white)}
.footer{left:0;top:583px;width:1200px;height:62px;background:var(--footer);color:var(--white);font-size:11px;display:flex;align-items:center;justify-content:center}
</style>
</head>
<body>
<header class="abs topbar"></header>
<div class="abs brand"><span class="brand-dot"></span><span class="brand-name">Keyhold</span></div>
<div class="abs btn btn-dashboard">
  <svg width="11" height="9" viewBox="0 0 11 9" fill="#fff"><rect x="0" y="0" width="3" height="2"/><rect x="4" y="0" width="3" height="2"/><rect x="8" y="0" width="3" height="2"/><rect x="0" y="3.5" width="3" height="2"/><rect x="4" y="3.5" width="3" height="2"/><rect x="8" y="3.5" width="3" height="2"/><rect x="0" y="7" width="3" height="2"/><rect x="4" y="7" width="3" height="2"/><rect x="8" y="7" width="3" height="2"/></svg>
  Dashboard</div>
<div class="abs btn btn-reports">
  <svg width="9" height="11" viewBox="0 0 9 11" fill="none" stroke="#fff" stroke-width="1"><path d="M.5.5h5l3 3v7h-8z"/><path d="M2 5.5h5M2 7.5h5"/></svg>
  Reports</div>
<nav class="abs nav">
  <span>Bach To Platform</span><span>Support</span><span>Work Order</span><span>Purchase Order</span><span>Complaince Management</span>
  <span>&nbsp;Login <svg width="11" height="11" viewBox="0 0 12 12" fill="none" stroke="#fff" stroke-width="1.2"><circle cx="6" cy="6" r="5.2"/><circle cx="6" cy="4.8" r="1.8"/><path d="M2.8 9.8c1.5-2 4.9-2 6.4 0"/></svg></span>
</nav>
<svg class="abs burger" width="17" height="14" viewBox="0 0 17 14" fill="#fff"><rect y="0" width="17" height="2.5"/><rect y="5.7" width="17" height="2.5"/><rect y="11.4" width="17" height="2.5"/></svg>

<section class="abs card activity"></section>
<div class="abs title-icon"><svg width="11" height="9" viewBox="0 0 11 9" fill="var(--blue)"><rect x="0" y="8" width="11" height="1"/><rect x="1" y="4" width="1.3" height="4"/><rect x="3.5" y="2" width="1.3" height="6"/><rect x="6" y="5" width="1.3" height="3"/><rect x="8.5" y="1" width="1.3" height="7"/></svg></div>
<h2 class="abs title" style="font-weight:400">Activity Overview</h2>
<div class="abs tabs">
  <span class="active">Last 7 Days</span><span>Last Months</span><span>Last 3 Months</span><span>Next 7 Days</span><span>Next Months</span><span>Next 3 Months</span>
</div>

<svg class="abs chart" width="827" height="400" font-family="Open Sans, sans-serif" font-size="11">
  <g stroke="var(--grid)" stroke-width="1">
    <line x1="88" y1="193" x2="785" y2="193"/><line x1="88" y1="227" x2="785" y2="227"/>
    <line x1="88" y1="262" x2="785" y2="262"/><line x1="88" y1="296" x2="785" y2="296"/>
    <line x1="88" y1="331" x2="785" y2="331"/><line x1="88" y1="365" x2="785" y2="365"/>
    <line x1="88" y1="184" x2="88" y2="365"/>
  </g>
  <g fill="var(--ink)" text-anchor="end">
    <text x="79" y="197">1.25</text><text x="72" y="231">1</text><text x="79" y="266">0.75</text>
    <text x="77" y="300">0.5</text><text x="79" y="335">0.25</text><text x="72" y="369">0</text>
  </g>
  <g fill="var(--ink)" text-anchor="middle">
    <text x="136" y="384">27-12-2020</text><text x="224" y="384">28-12-2020</text>
    <text x="313" y="384">29-12-2020</text><text x="401" y="384">30-12-2020</text>
    <text x="490" y="384">31-12-2020</text><text x="580" y="384">01-01-2021</text>
    <text x="668" y="384">02-01-2021</text><text x="756" y="384">03-01-2021</text>
  </g>
  <rect x="248.5" y="296" width="9.5" height="69" rx="4.75" fill="var(--orange)"/>
  <rect x="355.5" y="227" width="9.5" height="138" rx="4.75" fill="var(--blue)"/>
  <rect x="450.5" y="263" width="9.5" height="102" rx="4.75" fill="var(--pink)"/>
</svg>

<div class="legend">
  <span class="dot" style="left:59px;top:429px;background:var(--blue)"></span><span class="abs lbl" style="left:87px;top:427px;font-size:11px">Scheduled Maintenance</span>
  <span class="dot" style="left:263px;top:429px;background:var(--dark)"></span><span class="lbl" style="left:291px;top:428px">Scheduled Work Orders</span>
  <span class="dot" style="left:459px;top:429px;background:var(--violet)"></span><span class="lbl" style="left:488px;top:428px">Completed Work Orders</span>
  <span class="dot" style="left:664px;top:429px;background:var(--pink)"></span><span class="lbl" style="left:693px;top:428px">Property Inspections</span>
  <span class="dot" style="left:59px;top:460px;background:var(--violet)"></span><span class="lbl" style="left:87px;top:459px">Completed Scheduled Maintenance</span>
  <span class="dot" style="left:342px;top:460px;background:var(--orange)"></span><span class="lbl" style="left:370px;top:459px">Future Scheduled Maintenance</span>
  <span class="dot" style="left:613px;top:460px;background:var(--yellow)"></span><span class="lbl" style="left:642px;top:459px">Completed Property Inspections</span>
</div>

<aside class="abs card side"></aside>
<div class="abs stat" style="top:128px">
  <svg class="ring" width="54" height="54" viewBox="0 0 54 54"><circle cx="26" cy="27" r="25" fill="#fbc599"/><path d="M28 2a25 25 0 0 1 4 49" fill="none" stroke="var(--orange)" stroke-width="2"/><g fill="none" stroke="#fff" stroke-width="1.6"><circle cx="24" cy="24" r="7"/><path d="M29 29l7 7"/></g></svg>
  <div class="name">Vacancies Area</div><div class="value">188,500.00</div>
</div>
<div class="abs stat" style="top:259px">
  <svg class="ring" width="54" height="54" viewBox="0 0 54 54"><circle cx="26" cy="27" r="25" fill="#f6a5bb"/><path d="M28 2a25 25 0 0 1-14 47" fill="none" stroke="var(--pink)" stroke-width="2"/><path d="M17 26l9-8 9 8v10H17z" fill="none" stroke="#fff" stroke-width="1.5"/></svg>
  <div class="name">Rented Area</div><div class="value">233,500.00</div>
</div>
<div class="abs stat stat-total" style="top:390px">
  <svg class="ring" width="54" height="54" viewBox="0 0 54 54"><circle cx="26" cy="27" r="25" fill="#fff"/><text x="26" y="37" text-anchor="middle" font-size="28" fill="var(--violet)" font-family="Open Sans, sans-serif">&#931;</text></svg>
  <div class="name">Total Area</div><div class="value">420,000.00</div>
</div>

<footer class="abs footer">Copyrights 2021 Keyhold. All rights reserved</footer>
</body>
</html>
```